TK Stationery - Modern Contemporary

Develop modern template for Letterhead and Stationery (business card, letterhead, envelopes) using the TK Logo and Icon

Colors
0054AA
0677BA
7BADD7
CADEEF
E8F1F8
00AB8E
00BBA5
67D7C9
C6EFE9
E9F9F6
EE7325
F08F49
F5BC92
FAE3D3
FDF4ED
6B429C
8869AF
B7A5CE
E3DAEB
F3F0F8

```html
<!DOCTYPE html>
<html lang="en">
<head>
<meta charset="utf-8">
<title>Tallo Kera Letterhead</title>
<link rel="stylesheet" href="https://fonts.googleapis.com/css2?family=Arimo:wght@400&family=Mulish:wght@600;700;800&family=Prata&display=swap">
<style>
  :root {
    --backdrop: #cdcccd;
    --paper: #ffffff;
    --navy: #2b314d;
    --green: #3db377;
    --orange: #ef8433;
    --ink: #555557;
    --signature-tone: #e6e6e8;
  }
  * { box-sizing: border-box; margin: 0; padding: 0; }
  html, body {
    width: 1173px; height: 1200px; overflow: hidden;
    background: var(--backdrop);
  }
  .letterhead {
    position: absolute; left: 230px; top: 96px;
    width: 713px; height: 1008px;
    background: var(--paper);
    overflow: hidden;
  }
  .brand-name {
    position: absolute; top: 52px; left: 0; width: 100%;
    text-align: center;
    font-family: "Prata", serif; font-weight: 400;
    font-size: 32px; line-height: 40px;
    letter-spacing: 1px;
    color: var(--navy);
  }
  .salutation {
    position: absolute; left: 66px; top: 310px;
    font-family: "Mulish", sans-serif; font-weight: 700;
    font-size: 16px; line-height: 20px; color: var(--ink);
  }
  .letter-body {
    position: absolute; left: 64px; top: 357px; width: 582px;
    font-family: "Arimo", sans-serif; font-size: 11.4px;
    letter-spacing: 0.12px;
    line-height: 14.6px; color: var(--ink);
  }
  .letter-body p + p { margin-top: 13px; }
  .letter-body .line {
    display: block;
    text-align: justify;
    text-align-last: justify;
  }
  .letter-body .line.last { text-align-last: left; }
  .closing {
    position: absolute; left: 65px; top: 660px;
    font-family: "Mulish", sans-serif; font-weight: 800;
    font-size: 9px; line-height: 11px; color: var(--ink);
  }
  .signature {
    position: absolute; left: 64px; top: 702px; width: 117px; height: 34px;
    background: var(--signature-tone); border-radius: 4px;
  }
  .footer-band {
    position: absolute; left: 0; bottom: 0; width: 100%; height: 81px;
    display: flex;
  }
  .footer-band .band-left { flex: 1; background: var(--navy); }
  .footer-band .band-right { flex: 1; background: var(--green); }
  .footer-emblem {
    position: absolute; left: 309px; top: 920px;
    width: 96px; height: 96px;
  }
  .contact-list {
    position: absolute; left: 64px; top: 941px;
    list-style: none;
    font-family: "Arimo", sans-serif; font-size: 11.4px;
    line-height: 14.6px; color: #ffffff;
  }
  .contact-list li { display: flex; align-items: center; gap: 7px; }
  .contact-list svg { width: 9px; height: 9px; flex: none; }
  .address {
    position: absolute; right: 63px; top: 941px;
    text-align: right; font-style: normal;
    font-family: "Arimo", sans-serif; font-size: 11.4px;
    line-height: 14.6px; color: #ffffff;
  }
</style>
</head>
<body>
  <main class="letterhead">
    <h1 class="brand-name">tallo kera</h1>

    <p class="salutation">Dear Mr. Smith,</p>

    <section class="letter-body">
      <p>
        <span class="line">Lorem ipsum dolor sit amet, consectetuer adipiscing elit, sed diam nonmmy nibh euismod tincidunt ut laor</span>
        <span class="line">eet dolore magna aliquam erat volutpat. Ut wisi enim ad minim veniam, quis nostrud exerci tationmcorper</span>
        <span class="line">suscipit lobortis nisl ut aliquip ex ea commodo consequat. Duis autem vel eum iriure dolor in hendrerit in</span>
        <span class="line last">vulputate velit esse molestie consequat, vel illum dolore eu feugiat</span>
      </p>
      <p>
        <span class="line">Rorem ipsum dolor sit amet, consectetuer adipiscing elit, sed diam nonmmy nibh euismod tincidunt ut laor</span>
        <span class="line">eet dolore magna aliquam erat volutpat. Ut wisi enim ad minim veniam, quis nostrud exerci tationmcorper</span>
        <span class="line">suscipit lobortis nisl ut aliquip ex ea commodo consequat. Duis autem vel eum iriure dolor in hendrerit in</span>
        <span class="line last">vulputate velit esse molest</span>
      </p>
      <p>
        <span class="line">Dorem ipsum dolor sit amet, consectetuer adipiscing elit, sed diam nonmmy nibh euismod tincidunt ut laor</span>
        <span class="line">eet dolore magna aliquam erat volutpat. Ut wisi enim ad minim veniam, quis nostrud exerci tationmcorper</span>
        <span class="line">suscipit lobortis nisl ut aliquip ex ea commodo consequat. Duis autem vel eum iriure dolor in hendrerit in</span>
        <span class="line">suscipit lobortis nisl ut aliquip ex ea commodo consequat. Duis autem vel eum iriure dolor in hendrerit in</span>
        <span class="line last">vulputate velit esse molestie consequat, vel illum</span>
      </p>
      <p>
        <span class="line">Sorem ipsum dolor sit amet, consectetuer adipiscing elit, sed diam nonmmy nibh euismod tincidunt ut laor</span>
        <span class="line">eet dolore magna aliquam erat volutpat. Ut wisi enim ad minim veniam, quis nostrud exerci tationmcorper</span>
        <span class="line last">suscipit lobortis nisl ut aliquip ex ea commodo consequat. Duis autem vel eum iriure dolor in</span>
      </p>
    </section>

    <p class="closing">Sincerely,</p>
    <div class="signature" role="img" aria-label="Handwritten signature of the sender"></div>

    <div class="footer-band">
      <div class="band-left"></div>
      <div class="band-right"></div>
    </div>
    <svg class="footer-emblem" viewBox="0 0 96 96" aria-hidden="true">
      <circle cx="48" cy="48" r="48" fill="var(--paper)"/>
      <circle cx="48" cy="48" r="41" fill="var(--orange)"/>
    </svg>

    <ul class="contact-list">
      <li>
        <svg viewBox="0 0 10 10" aria-hidden="true"><path d="M2.2 0.8 L3.6 2.6 L2.8 3.6 Q3.8 5.6 6.2 7 L7.2 6.2 L9.2 7.6 L8.2 9.2 Q4.6 9 2.2 6 Q0.6 3.8 0.8 1.8 Z" fill="var(--green)"/></svg>
        <span>555-018-4420</span>
      </li>
      <li>
        <svg viewBox="0 0 10 10" aria-hidden="true"><rect x="0.5" y="2" width="9" height="6.5" fill="var(--green)"/><path d="M0.5 2 L5 5.6 L9.5 2" stroke="var(--navy)" stroke-width="0.9" fill="none"/></svg>
        <span>info@tallokera.com</span>
      </li>
      <li>
        <svg viewBox="0 0 10 10" aria-hidden="true"><circle cx="5" cy="5" r="4.5" fill="var(--green)"/><path d="M0.5 5 H9.5 M5 0.5 Q2.5 5 5 9.5 M5 0.5 Q7.5 5 5 9.5" stroke="var(--navy)" stroke-width="0.7" fill="none"/></svg>
        <span>www.tallokera.com</span>
      </li>
    </ul>

    <address class="address">
      Your address<br>
      city<br>
      state, ZIP 0000
    </address>
  </main>
</body>
</html>
```